Cruise Booking Website

Cruise search and booking website

This project is a redesign of a cruise booking website we did a few years ago.

The current website is located here: http://voyage.pylonworks.example/en/

It's not fully functional but gives you ad idea how miserable the old design was.

All the information about cruises, cruise lines, destinations, ports and shore excursions will be similar to http://www.sailquest.example/
Actual search pages (form, results, single result, sailing and cabin selection, ship info, booking) will have EXACTLY the same info as sailquest.example

We like the style of http://harborfleetdesk.example, it's quite modern, good spacing, not overloaded with information. So you can use it as an example of what we like, not what we want as a final result for us. Please, don't copy it. The result should not be possible to resemble the harborfleetdesk.example, because our site has to be unique. This is important!
If you submit a design that clearly reminds another cruise site it will be rejected!

Also the mockup provided is just to give you the basic structure and show what information has to be present on the page. It doesn't mean the layout has to be the same as a mockup. The layout is up to the designer.

I've updated the mockup to be more generic so it doesn't confuse you:
https://files.boxvault.example/s/k7m2qp9wz4hx/Home%20page.png

When you're adding social sharing icons like plazanet/chirpline you have to use chinese ones instead:
https://files.boxvault.example/s/t3nr8vx5lc2e/chinese-social-icons.png
Originals: http://minilk.example/qR7t

We'll start with home page first and after it's approved inner pages can be designed.

I know the cost of the project doesn't look high, but the task is straight forward and doesn't require to be very original, it's better to follow existing design and layout patterns that proved to work well.
That's why I encourage you to choose a template to build the design on top of one of https://themeparlor.example/ themes if it will save the design work, will be easier and faster for you. So it will be more like a customization than a new design from scratch.

Mockups, site map and logo files:
- https://files.boxvault.example/sh/h48dm2rs73fkpw/QvnbW2Xz8e

Website tree:
- https://sheets.papernest.example/document/d/7xPqR2mLw9sTk4VbN8cHj3YzA6eUf5GdKo1iMnBv/edit?usp=sharing
Updates

So far a lot of designs are just copying http://www.harborfleetdesk.example/ - we don't like it!

We like the style of harborfleetdesk.example, it's quite modern, good spacing, not overloaded with information. So you can use it as an example of what we like, not what we want as a final result for us. Please, don't copy it. The result should not be possible to resemble the harborfleetdesk.example, because our site has to be unique. This is important!

Target Market(s)

Chinese travellers

Industry/Entity Type

Build

Requirements
Must have
• * White, blue and red
* Large spacing, not too much information cramped into a small space like sailquest.example or the current website
* More "hidden" info in popups, tabs and so on, so not to many things are visible at the same time
* Compatible with kestrel scaffold styling (for easier coding):
- http://kestrelkit.codeshelf.example/scaffold/index.html
- http://skinmarket.example/
* Feel free to propose to build the design on top of one of https://themeparlor.example/ themes if it will save the design work, will be easier and faster for you

```html
<!DOCTYPE html>
<html lang="en">
<head>
<meta charset="utf-8">
<title>SeaCircle – Cruise Booking</title>
<link href="https://fonts.googleapis.com/css2?family=Open+Sans:ital,wght@0,400;0,600;0,700;1,400&display=swap" rel="stylesheet">
<style>
:root{
  --sky-top:#1f5ea8;
  --sky-mid:#7fa9d2;
  --sky-low:#2e6cb0;
  --topbar:#d7e4ee;
  --brand-blue:#2b6fae;
  --nav-active:#4cb3cc;
  --link-blue:#2a8fc6;
  --red:#e0284a;
  --red-phone:#e4475f;
  --dark-panel:#3b3e43;
  --tab-bg:#b9d0df;
  --content-bg:#f6f6f6;
  --footer-head:#245a93;
  --text:#222;
  --muted:#8a9aa8;
}
*{box-sizing:border-box;margin:0;padding:0}
html,body{width:1200px;height:1173px;overflow:hidden}
body{font-family:"Open Sans",Arial,sans-serif;color:var(--text);background:var(--sky-low)}
.stage{position:absolute;left:0;top:0;width:1400px;height:1369px;transform:scale(0.857142857);transform-origin:0 0;
  background:linear-gradient(180deg,var(--sky-top) 0%,#3f7cc0 30%,var(--sky-mid) 50%,#5a8fc8 62%,var(--sky-low) 70%,#1e5597 100%);overflow:hidden}
.page{position:absolute;left:200px;top:0;width:1001px;height:1369px;background:#fff}
.abs{position:absolute}

.topbar{left:0;top:0;width:1001px;height:31px;background:var(--topbar);font-size:13px;color:var(--muted)}
.topbar .links{position:absolute;right:30px;top:8px;color:#7f9ab2}
.topbar .links span{margin:0 12px}

.logo{left:22px;top:52px;display:flex;align-items:center;gap:12px}
.logo .mark{width:70px;height:70px;border-radius:50%;background:var(--brand-blue)}
.logo .name{font-size:46px;font-weight:700;color:var(--brand-blue);line-height:1;letter-spacing:-1px}
.logo .url{font-size:15px;font-weight:700;color:var(--brand-blue);margin-top:4px}
.phone{right:16px;top:58px;font-size:42px;font-weight:600;color:var(--red-phone);letter-spacing:-0.5px;white-space:nowrap}
.social{right:12px;top:111px;display:flex;gap:8px}
.social i{width:24px;height:24px;background:#d3d6d9;display:block}

.nav{left:0;top:152px;width:757px;height:51px;background:linear-gradient(#3479b8,#2a69a7);display:flex}
.nav a{flex:none;color:#fff;font-size:16px;text-decoration:none;height:51px;line-height:54px;text-align:center;border-right:1px solid #2660a0;white-space:nowrap}
.nav a.active{background:var(--nav-active)}
.nav-fill{left:757px;top:152px;width:244px;height:51px;background:linear-gradient(#3479b8,#2a69a7)}
.search{left:757px;top:158px;width:231px;height:40px;background:#e3e7ea;padding:3px}
.search .field{background:#fff;height:34px;width:188px;font-size:13px;font-style:italic;color:#888;padding:9px 16px;white-space:nowrap}
.search .go{position:absolute;right:3px;top:3px;width:38px;height:34px;background:var(--red)}

.hero{left:0;top:203px;width:701px;height:382px;
  background:linear-gradient(180deg,#142a4a 0%,#3b4d63 35%,#b07a45 62%,#e59a3c 72%,#6a4a35 88%,#2a2a30 100%)}
.hero-caption{left:0;top:495px;width:572px;height:75px;background:rgba(20,20,25,.72);color:#fff;font-size:35px;line-height:47px;font-weight:700;padding:14px 0 14px 29px;letter-spacing:-1.3px;white-space:nowrap;overflow:visible}

.finder{left:701px;top:203px;width:300px;height:382px;background:var(--dark-panel);color:#fff}
.finder h3{position:absolute;left:22px;top:38px;font-size:20px;font-weight:400;width:256px;padding-bottom:8px;border-bottom:1px solid #55585d}
.finder .dl{position:absolute;right:24px;top:42px}
.select{position:absolute;left:22px;width:255px;height:35px;background:linear-gradient(#fafafa,#e8e8e8);color:#2468a6;font-size:13px;padding:8px 10px;white-space:nowrap}
.select::after{content:"";position:absolute;right:0;top:0;width:34px;height:35px;border-left:1px solid #ccc}
.select svg{position:absolute;right:11px;top:10px;z-index:1}
.adv{position:absolute;left:17px;top:300px;font-size:13px;text-decoration:underline;color:#e6e6e6;white-space:nowrap}
.btn-search{position:absolute;left:126px;top:289px;width:153px;height:42px;background:var(--red);border:1px solid #b41d38;font-size:14px;padding:12px 12px;white-space:nowrap}

.tabs{left:0;top:585px;width:701px;height:58px;display:flex;background:var(--tab-bg)}
.tabs div{height:58px;line-height:62px;font-size:14px;text-align:center;border-right:2px solid #dce7ef;color:#222;white-space:nowrap}
.tabs .on{background:#fff}
.content{left:0;top:643px;width:701px;height:355px;background:var(--content-bg)}
.photo-frame{left:28px;top:41px;width:362px;height:231px;background:#e6e6e6;padding:5px}
.photo{width:352px;height:221px;background:linear-gradient(180deg,#4d8ad0 0%,#a9c9e6 38%,#6f9fc1 48%,#e6dccb 62%,#d2bd9c 100%)}
.book h2{position:absolute;left:404px;top:38px;font-size:30px;font-weight:400;color:var(--link-blue);white-space:nowrap}
.book p{position:absolute;left:407px;top:90px;width:270px;font-size:13px;line-height:20px}
.book ul{position:absolute;left:407px;top:143px;list-style:none}
.book li{font-size:14px;color:var(--link-blue);height:30px;display:flex;align-items:center;gap:11px;white-space:nowrap}
.book li svg{flex:none;margin-top:6px}

.news{left:701px;top:585px;width:300px;height:413px;background:repeating-linear-gradient(45deg,#d3e1eb 0 2px,#dae6ef 2px 4px)}
.news h3{position:absolute;left:34px;top:30px;font-size:21px;font-weight:400;color:var(--link-blue);white-space:nowrap}
.news .ship{position:absolute;left:33px;top:71px;width:238px;height:117px;background:linear-gradient(180deg,#5a9ee0 0%,#b6d6f1 55%,#2e6fb8 72%,#1d4f8f 100%)}
.news p{position:absolute;left:36px;top:201px;font-size:14px;line-height:20px;width:230px}
.input{position:absolute;left:36px;width:238px;height:38px;background:#fff;border:1px solid #cfd8de;font-size:14px;font-style:italic;color:#666;padding:10px 13px}
.subscribe{position:absolute;left:36px;top:349px;width:238px;height:37px;background:linear-gradient(#ea3456,#d31f41);color:#fff;font-size:18px;text-align:center;line-height:37px}
.subscribe svg{position:absolute;right:12px;top:9px}

.partners{left:0;top:998px;width:1001px;height:99px;background:#fff;border-top:1px solid #e4e4e4;overflow:hidden}
.partners .label{position:absolute;left:17px;top:15px;font-size:17px;color:#555;line-height:20px;white-space:nowrap}
.partners .label b{font-size:24px;font-weight:400;display:block}
.arrow{position:absolute;top:62px;width:30px;height:27px;background:#c6c6c6}
.arrow.r{background:#8e8e8e}
.arrow svg{position:absolute;left:11px;top:8px}
.strip{position:absolute;left:142px;top:0;width:2px;height:99px;background:#eef2f5}
.badge{position:absolute;top:21px;width:137px;height:55px;background:#fff;border:3px solid #e8e8e8;display:flex;align-items:center;justify-content:center}
.badge i{display:block;width:70px;height:16px;background:#c9d3dc;border-radius:3px}

.footer{left:0;top:1097px;width:1001px;height:272px;background:repeating-linear-gradient(45deg,#2a64a1 0 2px,#2d68a5 2px 4px);color:#fff}
.footer .band{position:absolute;left:0;top:0;width:1001px;height:53px;background:var(--footer-head)}
.footer h4{position:absolute;top:19px;font-size:18px;font-weight:700;white-space:nowrap}
.footer ul{position:absolute;top:57px;list-style:none;font-size:13px;line-height:22px;white-space:nowrap}
.about-logo{position:absolute;left:506px;top:62px;width:119px;height:97px;background:#fff;border:3px solid #dde6ee;display:flex;align-items:center;justify-content:center}
.about-logo i{width:70px;height:70px;border-radius:50%;background:var(--brand-blue);display:block}
.about-text{position:absolute;left:632px;top:61px;font-size:13px;line-height:17px;width:96px}
.contact{position:absolute;left:753px;top:56px;font-size:13px;line-height:20px;white-space:nowrap}
.contact .row{display:flex;align-items:center;gap:8px;margin-left:-3px}
.footer .rule{position:absolute;left:0;top:223px;width:1001px;height:1px;background:#3d77b3}
.copy{position:absolute;left:22px;top:243px;font-size:11px;white-space:nowrap}
</style>
</head>
<body>
<div class="stage">
 <div class="page">
  <div class="abs topbar"><div class="links">Sign in<span>|</span>sign up</div></div>

  <div class="abs logo">
   <div class="mark"></div>
   <div><div class="name">SeaCircle</div><div class="url">www.seacircle.example</div></div>
  </div>
  <div class="abs phone">4008 512 630</div>
  <div class="abs social"><i></i><i></i><i></i><i></i></div>

  <div class="abs nav-fill"></div>
  <nav class="abs nav">
   <a class="active" style="width:86px">Home</a><a style="width:77px">Lines</a><a style="width:86px">Shores</a><a style="width:129px">Destinations</a><a style="width:72px">FAQ</a><a style="width:75px">News</a><a style="width:123px">Promotions</a><a style="width:96px;border:none">Booking</a>
  </nav>
  <div class="abs search">
   <div class="field">Search website..</div>
   <div class="go"><svg width="38" height="34" viewBox="0 0 38 34"><circle cx="21" cy="15" r="7" fill="none" stroke="#fff" stroke-width="2.5"/><line x1="16" y1="20" x2="11" y2="26" stroke="#fff" stroke-width="2.5"/></svg></div>
  </div>

  <div class="abs hero" role="img" aria-label="Photo of a luxury yacht moored in a harbour at sunset"></div>
  <div class="abs hero-caption">All Inclusive Vacation Packages</div>

  <div class="abs finder">
   <h3>Find Your Cruise</h3>
   <svg class="dl" width="18" height="18" viewBox="0 0 18 18"><circle cx="9" cy="9" r="7.5" fill="none" stroke="#fff" stroke-width="1.5"/><path d="M9 4v8M5.5 9L9 12.5 12.5 9" fill="none" stroke="#fff" stroke-width="1.5"/></svg>
   <div class="select" style="top:87px">Popular Destinations<svg width="12" height="15"><path d="M1 6l5-5 5 5zM1 9l5 5 5-5z" fill="#444"/></svg></div>
   <div class="select" style="top:134px">Any Length<svg width="12" height="15"><path d="M1 6l5-5 5 5zM1 9l5 5 5-5z" fill="#444"/></svg></div>
   <div class="select" style="top:180px">Any Length<svg width="12" height="15"><path d="M1 6l5-5 5 5zM1 9l5 5 5-5z" fill="#444"/></svg></div>
   <div class="select" style="top:227px">&nbsp;Any Cruise Line<svg width="12" height="15"><path d="M1 6l5-5 5 5zM1 9l5 5 5-5z" fill="#444"/></svg></div>
   <div class="adv">Advanced Search</div>
   <div class="btn-search">Search Cruises
    <svg style="position:absolute;right:0;top:0" width="38" height="40" viewBox="0 0 38 40"><line x1="0" y1="0" x2="0" y2="40" stroke="#b41d38"/><circle cx="20" cy="18" r="6" fill="none" stroke="#fff" stroke-width="2"/><line x1="16" y1="23" x2="12" y2="28" stroke="#fff" stroke-width="2"/></svg>
   </div>
  </div>

  <div class="abs tabs">
   <div class="on" style="width:131px">Book with us</div>
   <div style="width:123px">Deals</div>
   <div style="width:123px">Pakages</div>
   <div style="width:123px">News</div>
   <div style="width:201px;border:none">First Time Cruiser?</div>
  </div>
  <div class="abs content book">
   <div class="abs photo-frame"><div class="photo" role="img" aria-label="Photo of a couple sitting together on a sandy beach facing the sea"></div></div>
   <h2>Book with us</h2>
   <p>We are the most advanced cruise booking provider in China</p>
   <ul>
    <li><svg width="14" height="14"><circle cx="7" cy="7" r="6" fill="none" stroke="#e0284a" stroke-width="1.6"/><path d="M7 4v6M4 7h6" stroke="#e0284a" stroke-width="1.6"/></svg>Great prices</li>
    <li><svg width="14" height="14"><circle cx="7" cy="7" r="6" fill="none" stroke="#e0284a" stroke-width="1.6"/><path d="M7 4v6M4 7h6" stroke="#e0284a" stroke-width="1.6"/></svg>Fast booking processing</li>
    <li><svg width="14" height="14"><circle cx="7" cy="7" r="6" fill="none" stroke="#e0284a" stroke-width="1.6"/><path d="M7 4v6M4 7h6" stroke="#e0284a" stroke-width="1.6"/></svg>20 cruise lines</li>
    <li><svg width="14" height="14"><circle cx="7" cy="7" r="6" fill="none" stroke="#e0284a" stroke-width="1.6"/><path d="M7 4v6M4 7h6" stroke="#e0284a" stroke-width="1.6"/></svg>Destinations around the world</li>
   </ul>
  </div>

  <div class="abs news">
   <h3>Cruise Deals Newsletter</h3>
   <div class="ship" role="img" aria-label="Photo of a large white cruise ship at sea"></div>
   <p>Subscribe an recive the beals cruise deals now!</p>
   <div class="input" style="top:252px">Name</div>
   <div class="input" style="top:299px">Email</div>
   <div class="subscribe">Subscribe<svg width="19" height="19"><circle cx="9.5" cy="9.5" r="8" fill="none" stroke="#fff" stroke-width="1.5"/><path d="M5 9.5h8M10 6.5l3 3-3 3" fill="none" stroke="#fff" stroke-width="1.5"/></svg></div>
  </div>

  <div class="abs partners">
   <div class="label">Our Reliable<b>Partners</b></div>
   <div class="arrow" style="left:56px"><svg width="8" height="11"><path d="M6 1L2 5.5 6 10" fill="none" stroke="#fff" stroke-width="1.6"/></svg></div>
   <div class="arrow r" style="left:88px"><svg width="8" height="11"><path d="M2 1l4 4.5L2 10" fill="none" stroke="#fff" stroke-width="1.6"/></svg></div>
   <div class="strip"></div>
   <div class="badge" style="left:156px"><i></i></div>
   <div class="badge" style="left:313px"><i></i></div>
   <div class="badge" style="left:471px"><i></i></div>
   <div class="badge" style="left:628px"><i></i></div>
   <div class="badge" style="left:785px"><i></i></div>
   <div class="badge" style="left:943px"><i></i></div>
  </div>

  <footer class="abs footer">
   <div class="band"></div>
   <h4 style="left:19px">Useful pages</h4>
   <h4 style="left:261px">Cruise info</h4>
   <h4 style="left:507px;top:17px">About us</h4>
   <h4 style="left:745px">Contact Us Today</h4>
   <ul style="left:23px"><li>About us</li><li>Contact us</li><li>FAQ</li><li>Terms of Service</li><li>Payment info</li><li>Reward points</li></ul>
   <ul style="left:266px"><li>Cruise news</li><li>Visa</li><li>Hunnymoon cruises</li><li>First time on a cruise?</li></ul>
   <div class="about-logo"><i></i></div>
   <div class="about-text">We are the most advanced cruise booking provider in China</div>
   <div class="contact">
    <div>Address, Place,</div><div>Postcode/zipcode</div><div>Country</div>
    <div class="row"><svg width="12" height="16"><path d="M3 1h3l1 4-2 1.5c.8 2 2 3.3 3.5 4L10 9l2 2v3c-5 1-11-6-9-13z" fill="#fff"/></svg>4008 512 630</div>
    <div class="row" style="margin-top:4px"><svg width="14" height="11"><rect x="0.5" y="0.5" width="13" height="10" fill="none" stroke="#fff"/><path d="M.5.5L7 6l6.5-5.5" fill="none" stroke="#fff"/></svg>info@seacircle.example</div>
   </div>
   <div class="rule"></div>
   <div class="copy">Copyright © 2013 SeaCircle. Use of this website constitutes acceptance of our User Agreement and Privacy Policy.</div>
  </footer>
 </div>
</div>
</body>
</html>
```